Create modern and sleek business card for luxury real estate company

We're a "boutique" real estate office looking for a design that gets across a highly modern luxury brand. Blacks and whites are probably the best colors unless we try a silver foil for the logo. I've attached a version of our current logo here. I'd like to swap out the current font on there with Gotham Light Regular.

I'm looking to have one side of the card have the logo with the space for our agents info on the other side.

Target Market(s)

Young professionals in a "luxury" headspace

Industry/Entity Type

Real estate

Contact Information for Business Card

A place for agent name, cell number, website. The slogan "Simply Rethinking Real Estate".

Font styles to use
Other font styles liked:
• Gotham Regular

Colors

Designer to choose only greyscale colors for use in the design.

Requirements
Must have
• Matte black as the background color. Clean lines and use of contrast. A specific design aspect that will use silver foil.
Nice to have
• Up in the air on integrating a QR code
Should not have
• Any houses or other real estate related design (ex: a clip art house)

```html
<!DOCTYPE html>
<html lang="en">
<head>
<meta charset="utf-8">
<title>Meridian Estates – Business Card</title>
<link href="https://fonts.googleapis.com/css2?family=Open+Sans:ital,wght@0,400;0,700;1,400&display=swap" rel="stylesheet">
<style>
  :root {
    --stage: #2a2a2a;
    --card: #141414;
    --card-edge: #0c0c0c;
    --pattern-dark: #101010;
    --pattern-light: #1c1c1c;
    --foil: #f2f2f2;
    --muted: #7d7d7d;
    --rule: #6a6a6a;
  }
  * { margin: 0; padding: 0; box-sizing: border-box; }
  html, body { width: 1200px; height: 900px; overflow: hidden; }
  body {
    background: var(--stage);
    font-family: "Open Sans", Arial, sans-serif;
    color: var(--foil);
    position: relative;
  }
  .card {
    position: absolute;
    left: 285px;
    width: 630px;
    height: 360px;
    background: var(--card);
    border: 1px solid var(--card-edge);
    box-shadow: 0 10px 30px rgba(0,0,0,.45);
    overflow: hidden;
  }
  .card--front { top: 60px; }
  .card--back { top: 480px; }

  /* Front */
  .brand {
    position: absolute;
    left: 250px;
    top: 70px;
    display: flex;
    align-items: center;
    gap: 18px;
  }
  .brand__disc {
    width: 82px; height: 82px;
    border: 3px solid var(--foil);
    border-radius: 50%;
  }
  .brand__name {
    font-weight: 400;
    font-size: 36px;
    line-height: 1.05;
    letter-spacing: 2px;
    color: var(--foil);
    text-transform: uppercase;
  }
  .agent {
    position: absolute;
    right: 360px;
    top: 208px;
    text-align: right;
  }
  .agent__name {
    font-weight: 700;
    font-size: 19px;
    letter-spacing: 1px;
    text-transform: uppercase;
  }
  .agent__title {
    font-style: italic;
    font-size: 15px;
    color: var(--muted);
    margin-top: 2px;
  }
  .divider {
    position: absolute;
    left: 290px;
    top: 205px;
    width: 1px;
    height: 78px;
    background: var(--rule);
  }
  .contact {
    position: absolute;
    left: 310px;
    top: 206px;
    list-style: none;
    font-size: 16px;
    line-height: 25px;
  }
  .contact li { display: flex; align-items: center; gap: 8px; }
  .contact svg { width: 12px; height: 12px; fill: var(--muted); flex: none; }

  /* Back */
  .pattern {
    position: absolute;
    inset: 0;
    background: linear-gradient(135deg, var(--pattern-light), var(--pattern-dark));
  }
  .back-mark {
    position: absolute;
    right: 36px;
    bottom: 30px;
    display: flex;
    align-items: center;
    gap: 10px;
  }
  .back-mark__disc {
    width: 38px; height: 38px;
    border: 2px solid var(--foil);
    border-radius: 50%;
  }
  .back-mark__name {
    font-size: 14px;
    letter-spacing: 1.5px;
    text-transform: uppercase;
    color: var(--foil);
  }
</style>
</head>
<body>

<section class="card card--front">
  <div class="brand">
    <div class="brand__disc"></div>
    <div class="brand__name">Meridian<br>Estates</div>
  </div>

  <div class="agent">
    <div class="agent__name">Dorian Hale</div>
    <div class="agent__title">President</div>
  </div>

  <div class="divider"></div>

  <ul class="contact">
    <li>
      <svg viewBox="0 0 12 12"><path d="M2.5 0.8l2 2-1 1.4c.6 1.4 1.9 2.7 3.3 3.3l1.4-1 2 2-1.2 1.9C5 10.4 1.6 7 .6 2z"/></svg>
      555-014-2287
    </li>
    <li>
      <svg viewBox="0 0 12 12"><path d="M0 2.5h12v7H0z M0 2.5l6 4 6-4" /></svg>
      info@meridianestates.com
    </li>
    <li>
      <svg viewBox="0 0 12 12"><circle cx="6" cy="6" r="5.5"/></svg>
      www.meridianestates.com
    </li>
  </ul>
</section>

<section class="card card--back">
  <div class="pattern" role="img" aria-label="Repeating embossed brand monogram pattern in matte black"></div>
  <div class="back-mark">
    <div class="back-mark__disc"></div>
    <span class="back-mark__name">Meridian Estates</span>
  </div>
</section>

</body>
</html>
```